New, modern business card for growing audiology practice

We need a new business card for our audiology practice. Our logo and website have recently changed (more modern) and we want our business cards to reflect this change.
We conduct hearing tests, perform earwax removals, and fit & dispense hearing aids to our patients. We are a family owned practice in which the owner is the one who works directly with the patient. I have attached logos in various formats to use, as well as two ideas I found on this website; as well as a scanned copy of our current logo. Good luck!

Industry/Entity Type

Business

Contact Information for Business Card

Company name: Tolvera Hearing Center
Provider name: Peter Wolstenby, Au.D. F/NSB
Phone number: (440) 683-5127
Address: 837 W. Lindell Ave. Brenmoor Falls, OH 44790
email: tolverahearing@postvane.com
website: tolverahearing.com

Colors
000000
aaaaaa
dbdbdb
cacaca
9bcb3c
afd23c
cadf82
b1b1b1

Requirements
Must have
• My card must include information in the "details" section. In the attached images, I found a few that I liked and I would like to model after - "brisky bouncin'" and "Sound Method Center".
• Must be horizontal.
• Must include logos provided. I uploaded them in various file formats and various ways.
• Must match logo font, if possible, if not, please get as close as you can.
Nice to have
• I really like the idea of having a color on one side with just the logo and company name and the contact information and provider name on the other side. I also really like the idea of having the main color dominating on the logo/company side with accent of that same color on the contact side of the card.
Should not have
• Must not be vertical.

```html
<!DOCTYPE html>
<html lang="en">
<head>
<meta charset="utf-8">
<title>Tolvera Hearing Center – Business Card</title>
<link rel="stylesheet" href="https://fonts.googleapis.com/css2?family=Cabin:wght@400&family=Roboto:wght@400;500&family=Roboto+Condensed:wght@700&display=swap">
<style>
  :root {
    --backdrop: #262626;
    --brand-green: #709e37;
    --card-white: #f2f2f2;
    --ink: #111111;
    --ink-soft: #555555;
    --paper-text: #ffffff;
  }
  * { margin: 0; padding: 0; box-sizing: border-box; }
  html, body {
    width: 1200px;
    height: 960px;
    overflow: hidden;
    background: var(--backdrop);
  }
  .card {
    position: absolute;
    left: 320px;
    width: 600px;
    border-radius: 22px;
    overflow: hidden;
  }
  .card-front {
    top: 105px;
    height: 345px;
    background: var(--brand-green);
  }
  .card-back {
    top: 493px;
    height: 342px;
    background: var(--card-white);
  }
  .wordmark {
    font-family: "Cabin", "Gill Sans", sans-serif;
    font-weight: 400;
    white-space: nowrap;
    display: flex;
    align-items: center;
    gap: 10px;
  }
  .wordmark .dot {
    width: 14px;
    height: 14px;
    border-radius: 50%;
    flex: none;
  }
  .card-front .wordmark {
    position: absolute;
    left: 0; right: 0;
    top: 155px;
    justify-content: center;
    font-size: 30px;
    color: var(--paper-text);
    letter-spacing: 0.5px;
  }
  .card-front .wordmark .dot { background: var(--paper-text); }
  .front-web {
    position: absolute;
    left: 0; right: 0;
    top: 288px;
    text-align: center;
    font-family: "Roboto", sans-serif;
    font-size: 14px;
    letter-spacing: 4.2px;
    color: var(--paper-text);
  }
  .back-accent {
    position: absolute;
    left: -150px;
    top: 20px;
    width: 380px;
    height: 380px;
    border-radius: 50%;
    border: 28px solid var(--brand-green);
  }
  .card-back .wordmark {
    position: absolute;
    right: 32px;
    top: 33px;
    font-size: 21px;
    color: var(--ink);
    gap: 8px;
  }
  .card-back .wordmark .dot { background: var(--brand-green); width: 12px; height: 12px; }
  .provider {
    position: absolute;
    right: 30px;
    top: 151px;
    text-align: right;
  }
  .provider-name {
    font-family: "Roboto Condensed", sans-serif;
    font-weight: 700;
    font-size: 22px;
    color: var(--brand-green);
    line-height: 26px;
  }
  .provider-title {
    font-family: "Roboto", sans-serif;
    font-weight: 500;
    font-size: 15px;
    color: var(--ink);
    letter-spacing: 0.5px;
    line-height: 20px;
  }
  .address {
    position: absolute;
    right: 30px;
    top: 207px;
    text-align: right;
    font-family: "Roboto", sans-serif;
    font-size: 14.5px;
    line-height: 18px;
    color: var(--ink-soft);
    font-style: normal;
  }
  .contacts {
    position: absolute;
    right: 30px;
    top: 254px;
    list-style: none;
    font-family: "Roboto", sans-serif;
    font-size: 14.5px;
    line-height: 19px;
    color: var(--ink-soft);
  }
  .contacts li {
    display: flex;
    justify-content: flex-end;
    align-items: center;
    gap: 12px;
  }
  .contacts svg { width: 13px; height: 13px; flex: none; fill: var(--brand-green); }
</style>
</head>
<body>

<section class="card card-front" aria-label="Card front">
  <div class="wordmark"><span class="dot"></span>TOLVERA HEARING CENTER</div>
  <p class="front-web">www.tolverahearing.com</p>
</section>

<section class="card card-back" aria-label="Card back">
  <div class="back-accent" aria-hidden="true"></div>
  <div class="wordmark"><span class="dot"></span>TOLVERA HEARING CENTER</div>

  <div class="provider">
    <p class="provider-name">PETER WOLSTENBY</p>
    <p class="provider-title">AU.D. F/NSB</p>
  </div>

  <address class="address">
    837 W. Lindell Ave.<br>
    Brenmoor Falls, OH 44790
  </address>

  <ul class="contacts">
    <li>(440) 683-5127
      <svg viewBox="0 0 24 24" aria-hidden="true"><path d="M6.6 10.8a15.1 15.1 0 0 0 6.6 6.6l2.2-2.2c.3-.3.7-.4 1-.2 1.1.4 2.3.6 3.6.6.6 0 1 .4 1 1V20c0 .6-.4 1-1 1A17 17 0 0 1 3 4c0-.6.4-1 1-1h3.5c.6 0 1 .4 1 1 0 1.3.2 2.5.6 3.6.1.3 0 .7-.2 1z"/></svg>
    </li>
    <li>tolverahearing@postvane.com
      <svg viewBox="0 0 24 24" aria-hidden="true"><path d="M2 5h20v14H2z" opacity=".9"/><path d="M2 5l10 8 10-8" fill="none" stroke="#f2f2f2" stroke-width="2"/></svg>
    </li>
    <li>tolverahearing.com
      <svg viewBox="0 0 24 24" aria-hidden="true"><circle cx="12" cy="12" r="10"/><path d="M2 12h20M12 2c3 3 3 17 0 20M12 2c-3 3-3 17 0 20" fill="none" stroke="#f2f2f2" stroke-width="1.6"/></svg>
    </li>
  </ul>
</section>

</body>
</html>
```